Product Label Design

Need a product design for our Epsom salt product, needs to have a luxurious simple feel to it. The picture attached is our brand and wordage on it, the bag we think should be a stand up bag that should be offwhite/creme color. The other picture are products that we like. We updated the packaging to be a Kraft tube box, please see the attached photo for dimensions.

```html
<!DOCTYPE html>
<html lang="en">
<head>
<meta charset="UTF-8">
<title>Calma Terra Premium Epsom Salt – Pouch Front</title>
<link href="https://fonts.googleapis.com/css2?family=Playfair+Display:wght@900&family=Cinzel:wght@700&family=Montserrat:wght@400;700&display=swap" rel="stylesheet">
<style>
  :root {
    --backdrop: #e3e3e3;
    --pouch: #f3f2f0;
    --pouch-edge: #e6e5e2;
    --seal: #ebeae7;
    --sprig-tone: #e4e3e0;
    --ink: #111111;
    --ink-soft: #222222;
  }
  * { margin: 0; padding: 0; box-sizing: border-box; }
  html, body {
    width: 1200px;
    height: 800px;
    overflow: hidden;
  }
  body {
    background: var(--backdrop);
    position: relative;
    font-family: "Montserrat", sans-serif;
    color: var(--ink);
  }
  .pouch-front {
    position: absolute;
    left: 459px;
    top: 214px;
    width: 282px;
    height: 442px;
    background: linear-gradient(90deg, var(--pouch-edge) 0%, var(--pouch) 12%, var(--pouch) 88%, var(--pouch-edge) 100%);
    border-radius: 3px 3px 6px 6px;
  }
  .pouch-seal {
    position: absolute;
    left: 0;
    top: 0;
    width: 100%;
    height: 40px;
    background: var(--seal);
    border-bottom: 1px solid var(--pouch-edge);
  }
  .label {
    position: absolute;
    left: 0;
    top: 0;
    width: 100%;
    height: 100%;
    text-align: center;
  }
  .sprig-ornament {
    position: absolute;
    left: 101px;
    top: 104px;
    width: 80px;
    height: 18px;
    background: var(--sprig-tone);
    border-radius: 3px;
  }
  .brand-name {
    position: absolute;
    left: 0;
    width: 100%;
    top: 132px;
    font-family: "Playfair Display", serif;
    font-weight: 900;
    font-size: 26px;
    line-height: 1;
  }
  .product-tier {
    position: absolute;
    left: 0;
    width: 100%;
    top: 176px;
    font-family: "Cinzel", serif;
    font-weight: 700;
    font-size: 18px;
    line-height: 1;
    letter-spacing: 0.5px;
  }
  .product-name {
    position: absolute;
    left: 0;
    width: 100%;
    top: 197px;
    font-family: "Cinzel", serif;
    font-weight: 700;
    font-size: 27px;
    line-height: 1;
  }
  .tagline {
    position: absolute;
    left: 62px;
    width: 157px;
    top: 241px;
    height: 21px;
    border-top: 1px solid var(--ink);
    border-bottom: 1px solid var(--ink);
    font-size: 10.5px;
    line-height: 19px;
    letter-spacing: 0.3px;
  }
  .benefits {
    position: absolute;
    left: 83px;
    width: 115px;
    top: 266px;
    list-style: none;
  }
  .benefits li {
    font-size: 7.2px;
    line-height: 19.5px;
    height: 21px;
    border-bottom: 1px solid var(--ink-soft);
    white-space: nowrap;
  }
  .benefits li.benefit-last {
    border-bottom: none;
    font-size: 8.6px;
  }
  .cert-badge {
    position: absolute;
    left: 81px;
    top: 345px;
    width: 20px;
    height: 20px;
  }
  .net-weight {
    position: absolute;
    left: 137px;
    top: 351px;
    font-size: 6.6px;
    font-weight: 700;
    white-space: nowrap;
  }
</style>
</head>
<body>
  <div class="pouch-front">
    <div class="pouch-seal"></div>
    <div class="label">
      <div class="sprig-ornament" role="img" aria-label="Small leaf sprig ornament between two short rules"></div>
      <div class="brand-name">Calma Terra</div>
      <div class="product-tier">PREMIUM</div>
      <div class="product-name">EPSOM SALT</div>
      <div class="tagline">SOOTHE . RELAX . REVIVE</div>
      <ul class="benefits">
        <li>MAGESIUM SULFATE CRYSTALS</li>
        <li>DETOXIFY &amp; DESTRESS</li>
        <li>RELIEVES SORE MUSCLES</li>
        <li class="benefit-last">Therapeutic Bath Soak</li>
      </ul>
      <svg class="cert-badge" viewBox="0 0 20 20" role="img" aria-label="Certification badge placeholder">
        <circle cx="10" cy="10" r="9" fill="none" stroke="#111111" stroke-width="1.2"/>
      </svg>
      <div class="net-weight">NET WT.2LBS(907)g</div>
    </div>
  </div>
</body>
</html>
```